wardrobe/costume stylist needs good business card for own business

Hi:)

I'm wanting a business card for my company. I am a freelance stylist.

I do wardrobe/costume stylist to TV commercials; Films; Fashion and Lifestyle shoots.

I'd like a design based around my name Rosalind Parfrey written nicely, maybe a colour? Up to you?!

I've attached a couple of images of business cards I like
.... be creative and have fun!

Thank you :)

Reason: I was trying to get my new business card ready for before I headed overseas Friday morning but I don't think that was realistic so I'd like to extend the deadline to give time to the project. Thank you

Hi designers:) Thank you for all your designs, I've extended the deadline until Sunday, so there's a bit more time. I've attached 3 pictures of business cards which I quite like, please take a look to see if it can be of help in your process. I like the pale plain or patterned background with dark font and the dark plain or patterned background with the pale font the motifs the feminine fonts the plain fonts I like the idea of playing with a circle or some shape on one side of the card with my name or initials as in the picture I have on my post could you play around with this idea a bit please? Thank you all for the work you've done :) Rosa

Hi I am working overseas til Saturday night sorry for no feedback until I teturn Thanks :) Rosa

Hi designers, Thank you all so much for submitting your designs, I really appreciate your input into my project :) I'm sorry I didn't get to respond to some comments, and give feedback. I didn't back from being away until later than I expected, and the deadline had passed then, so apologies. Thanks to you all again for all your really good designs :) Rosa

Target Market(s)

I am a freelance stylist my target audience is producers, production companies, photographers, directors...

Industry/Entity Type

Business

Requirements
Must have
• Rosalind Parfrey
Stylist or Wardrobe Stylist

email rosaparfrey@mailbox-example.co.nz
Mobile 0218467193

(Don't have to use the words 'email' and 'mobile')
Nice to have
• Would like it to be double sided
Like B & W
Like pale colour background with dark font or white font
Like dark colour background with pale font
Should not have
• I would prefer it not to incorporate pictures

```html
<!DOCTYPE html>
<html lang="en">
<head>
<meta charset="utf-8">
<title>Rosalind Parfrey – Stylist Business Card</title>
<link rel="stylesheet" href="https://fonts.googleapis.com/css2?family=Pinyon+Script&family=Cormorant+Garamond:wght@500&display=swap">
<style>
  :root {
    --page: #ffffff;
    --mint: #b3e1cb;
    --mint-light: #eef8f3;
    --mint-faint: #a6d9c1;
    --ink: #161616;
  }
  html, body {
    margin: 0;
    padding: 0;
    overflow: hidden;
    background: var(--page);
  }
  .canvas {
    position: relative;
    width: 1200px;
    height: 900px;
    overflow: hidden;
    background: var(--page);
  }
  .card {
    position: absolute;
    top: 290px;
    width: 540px;
    height: 320px;
    border-radius: 28px;
    background: var(--mint);
    overflow: hidden;
    box-shadow: 0 10px 24px rgba(0, 0, 0, 0.12);
  }
  .card--front {
    left: 40px;
    background: radial-gradient(ellipse at 55% 50%, var(--mint-light) 0%, #d3eee0 40%, var(--mint) 80%);
  }
  .card--back {
    left: 620px;
  }
  .ornament {
    position: absolute;
    left: 50%;
    transform: translateX(-50%);
    width: 160px;
    height: 56px;
    background: var(--ink);
    border-radius: 50% 50% 40% 40% / 60% 60% 40% 40%;
    opacity: 0.88;
  }
  .ornament--top { top: 40px; }
  .ornament--bottom { bottom: 40px; border-radius: 40% 40% 50% 50% / 40% 40% 60% 60%; }
  .brand {
    position: absolute;
    left: 0;
    right: 0;
    top: 108px;
    text-align: center;
    color: var(--ink);
  }
  .brand__name {
    display: block;
    font-family: "Pinyon Script", cursive;
    font-size: 60px;
    line-height: 70px;
    font-weight: 400;
  }
  .brand__role {
    display: block;
    margin-top: -10px;
    font-family: "Cormorant Garamond", serif;
    font-size: 17px;
    letter-spacing: 6px;
    font-weight: 500;
  }
  .watermark {
    position: absolute;
    left: 90px;
    top: 10px;
    width: 300px;
    height: 300px;
    border-radius: 50%;
    background: var(--mint-faint);
    opacity: 0.45;
  }
  .monogram {
    position: absolute;
    left: 0;
    right: 0;
    top: 40px;
    text-align: center;
    font-family: "Pinyon Script", cursive;
    font-size: 62px;
    line-height: 70px;
    color: var(--ink);
  }
  .contact {
    position: absolute;
    left: 0;
    right: 0;
    top: 172px;
    text-align: center;
    font-family: "Cormorant Garamond", serif;
    font-weight: 500;
    color: var(--ink);
  }
  .contact__line {
    display: block;
    font-size: 20px;
    line-height: 30px;
    letter-spacing: 3px;
  }
  .contact__line--email {
    font-size: 18px;
    letter-spacing: 1.5px;
  }
</style>
</head>
<body>
  <main class="canvas">
    <section class="card card--front" aria-label="Card front">
      <div class="ornament ornament--top" role="img" aria-label="Decorative damask flourish"></div>
      <h1 class="brand">
        <span class="brand__name">Rosalind Parfrey</span>
        <span class="brand__role">Stylist</span>
      </h1>
      <div class="ornament ornament--bottom" role="img" aria-label="Decorative damask flourish"></div>
    </section>

    <section class="card card--back" aria-label="Card back">
      <div class="watermark" role="img" aria-label="Faint large monogram decoration"></div>
      <div class="monogram">RP</div>
      <address class="contact" style="font-style: normal;">
        <span class="contact__line">0218467193</span>
        <span class="contact__line contact__line--email">rosaparfrey@mailbox-example.co.nz</span>
      </address>
    </section>
  </main>
</body>
</html>
```